Web landing page design

- Create a Web Design (Uncoded - PSD layout only)

We need a single web page design to promote our service. This page will
acts as a landing page for users and also be utilized in social media
advertising. Please provide us with a cutting edge design. I have attached
a link for what the company is about. In essence we are a photo checking
service which reviews photos for retailers, hotels abd car dealerships to
check everything is good after a service has been performed. Whether it be
a new promotion, cleaning or just checking prices. I am looking for a
design to say that we do many photos and at a very cost effective price
(team based in Mexico)

Link: https://slidevault.example/view/qTr8nWx2LpZk4mHcYdJs/
*Deadline*
5 days
*Updates*

- The Start Here box needs to look like this:

-Start Here (heading)
-A box for email addresses to be entered
-Then a check box with "Yes, I have read and agree to the Privacy Policy
and agree to receive email marketing from Plumora88'
-A submit button

All of this information needs to be in one box please. And please feel
free to contact me if you have any questions about this.

*Target Market(s)*
Retail business, Merchandising companies, Rental property owners, Car
dealers
Updates

Please can you submit entries. I am just looking for a tidy to a presentation already created. Just needs design touches.

Target Market(s)

Ability for audience to understand concept quickly
Benefits to why to use the product stand out
Technology driven approach

Industry/Entity Type

Retail

Number of Pages Required

1 page

Colors
0792cd

Requirements
Must have
• Clean and modern design

```html
<!DOCTYPE html>
<html lang="en">
<head>
<meta charset="utf-8">
<title>Lumetra – Transform retail execution</title>
<link rel="stylesheet" href="https://fonts.googleapis.com/css2?family=Open+Sans:wght@400;600;700&display=swap">
<style>
:root{
  --brand:#0792cd;
  --brand-deep:#1a7fc4;
  --brand-bright:#18a0f5;
  --ink:#222;
  --muted:#555;
  --white:#fff;
  --band:#f2f2f2;
  --rule:#d6d6d6;
}
*{margin:0;padding:0;box-sizing:border-box}
html,body{width:1200px;height:946px;overflow:hidden;background:var(--white);font-family:"Open Sans",sans-serif}
.page{position:relative;width:1200px;height:946px}
.hero{position:absolute;left:0;top:0;width:1200px;height:643px;overflow:hidden}
.hero-photo{position:absolute;inset:0;
  background:
    radial-gradient(ellipse 340px 240px at 1030px 470px,rgba(190,40,40,.75),transparent 70%),
    radial-gradient(ellipse 300px 260px at 420px 400px,rgba(170,120,100,.55),transparent 70%),
    radial-gradient(ellipse 420px 260px at 820px 180px,rgba(70,110,40,.7),transparent 70%),
    radial-gradient(ellipse 300px 200px at 120px 330px,rgba(120,100,40,.5),transparent 70%),
    linear-gradient(160deg,#2c3a22 0%,#3b4a2c 40%,#4a3a2a 70%,#3a2420 100%)}
.hero-shade{position:absolute;inset:0;background:rgba(10,20,30,.28)}
.brand{position:absolute;left:70px;top:60px;display:flex;align-items:center;gap:10px}
.brand-dot{width:18px;height:18px;border-radius:50%;background:var(--brand)}
.brand-name{font-size:38px;font-weight:700;color:var(--white);line-height:1}
.nav{position:absolute;top:23px;left:671px;display:flex;align-items:center}
.nav a{color:var(--white);text-decoration:none;font-size:16px;font-weight:700;position:absolute;white-space:nowrap;transform:translateX(-50%);top:32px}
.nav .active{top:0;left:42px;width:84px;height:84px;border-radius:50%;background:var(--brand-deep);display:flex;align-items:center;justify-content:center}
.headline{position:absolute;top:172px;left:0;width:1188px;text-align:center;color:var(--white);font-size:50px;font-weight:600;line-height:54px}
.signup{position:absolute;top:322px;left:229px;width:741px;text-align:center}
.signup h2{font-size:50px;font-weight:700;color:var(--brand-bright);line-height:66px;margin-bottom:20px}
.email{display:block;width:741px;height:67px;border:0;border-radius:34px;background:var(--white);padding:0 25px;font:400 14px "Open Sans",sans-serif;color:#555}
.email::placeholder{color:#555}
.consent{display:flex;align-items:center;gap:9px;margin:25px 0 0 16px;color:var(--white);font-size:14px;font-weight:600;text-align:left}
.tick{width:15px;height:15px;flex:none}
.submit{display:block;margin:32px auto 0;width:218px;height:55px;border:0;border-radius:28px;background:var(--brand-bright);color:var(--white);font:700 18px "Open Sans",sans-serif}
.stats{position:absolute;top:643px;left:0;width:1200px;height:216px;background:var(--band);border-top:1px solid var(--rule);border-bottom:1px solid var(--rule);display:grid;grid-template-columns:333px 260px 280px 327px}
.stat{text-align:center;border-right:1px solid var(--rule);padding-top:32px}
.stat:last-child{border-right:0}
.stat svg{width:34px;height:34px;display:block;margin:0 auto}
.stat-value{font-size:36px;font-weight:700;color:var(--ink);line-height:50px;margin-top:10px}
.stat-value.accent{color:var(--brand-deep)}
.stat-label{font-size:18px;font-weight:600;color:var(--muted);line-height:24px;margin-top:4px}
.footer{position:absolute;top:897px;left:0;width:1200px;text-align:center;font-size:14px;font-weight:600;color:var(--ink)}
</style>
</head>
<body>
<div class="page">
  <section class="hero">
    <div class="hero-photo" role="img" aria-label="Hand holding a smartphone to photograph a blurred fresh produce display in a store"></div>
    <div class="hero-shade"></div>
    <div class="brand"><span class="brand-name">Lumetra</span><span class="brand-dot"></span></div>
    <nav class="nav">
      <a class="active" href="#about">About</a>
      <a href="#results" style="left:150px">Results</a>
      <a href="#how" style="left:259px">How</a>
      <a href="#trial" style="left:368px">Free Trial</a>
    </nav>
    <h1 class="headline">Transform retail execution<br>with a simple photo</h1>
    <form class="signup">
      <h2>Start Here</h2>
      <input class="email" type="email" placeholder="Enter Your Email Address">
      <label class="consent">
        <svg class="tick" viewBox="0 0 15 15"><rect x=".5" y=".5" width="14" height="14" fill="#fff" stroke="#888"/><path d="M3.5 7.5l3 3 5-6" fill="none" stroke="#1a7fc4" stroke-width="2"/></svg>
        Yes, I have read and agree to the Privacy Policy and agree to receive email marketing from Plumora88
      </label>
      <button class="submit" type="button">Submit</button>
    </form>
  </section>

  <section class="stats">
    <div class="stat">
      <svg viewBox="0 0 34 34"><rect x="2" y="4" width="30" height="26" fill="none" stroke="#1a7fc4" stroke-width="2.5"/><circle cx="23" cy="12" r="3" fill="#1a7fc4"/><path d="M5 27l9-10 6 6 4-4 6 8z" fill="#1a7fc4"/></svg>
      <div class="stat-value accent">2.2M</div>
      <div class="stat-label">Photos Reviewed<br>Last Year</div>
    </div>
    <div class="stat">
      <svg viewBox="0 0 34 34"><path d="M17 2l4.4 9.6 10.4 1.1-7.8 7 2.2 10.3L17 24.8 7.8 30l2.2-10.3-7.8-7 10.4-1.1z" fill="none" stroke="#222" stroke-width="2" stroke-linejoin="round"/></svg>
      <div class="stat-value">5P</div>
      <div class="stat-label">From per photo<br>reviewed</div>
    </div>
    <div class="stat">
      <svg viewBox="0 0 34 34"><rect x="6" y="4" width="22" height="28" rx="2" fill="none" stroke="#222" stroke-width="2.5"/><rect x="12" y="1.5" width="10" height="5" fill="#222"/><path d="M10 13h14M10 18h14M10 23h14M10 28h14" stroke="#222" stroke-width="2"/></svg>
      <div class="stat-value">97.2%</div>
      <div class="stat-label">Average<br>Compliance</div>
    </div>
    <div class="stat">
      <svg viewBox="0 0 34 34"><rect x="4" y="2" width="26" height="30" fill="none" stroke="#222" stroke-width="2.5"/><rect x="10" y="17" width="3" height="10" fill="#222"/><rect x="15.5" y="11" width="3" height="16" fill="#222"/><rect x="21" y="14" width="3" height="13" fill="#222"/></svg>
      <div class="stat-value">3-8%</div>
      <div class="stat-label">Sales<br>Increase</div>
    </div>
  </section>

  <footer class="footer">© 2018 Company Name |&nbsp; All Rights Reserved</footer>
</div>
</body>
</html>
```